Meridale Partners Website

Meridale Partners (MP) provide Analytics & Enterprise Performance Management (EPM) advisory & consultancy services. We are passionate about data and making a difference for our clients by working in partnership with them, helping them on their journey to becoming an Meridale Partner. We deliver insights which give our clients a competitive edge and a much deeper understanding of their organisation.

We need a website which shows who we are, what we do and how we do it.

www.meridale-partners.example is our very basic website at the moment. We want to completely revamp it with a corporate look

```html
<!DOCTYPE html>
<html lang="en">
<head>
<meta charset="utf-8">
<title>Meridale Partners – Data Analytics &amp; EPM Consulting</title>
<link href="https://fonts.googleapis.com/css2?family=Montserrat:wght@600;700;800&family=Roboto:wght@400;500;700&display=swap" rel="stylesheet">
<style>
:root{
  --navy:#2b5570;
  --navy-dark:#1f4259;
  --orange:#e5843a;
  --ice:#eaf5fc;
  --ink:#1d1d1f;
  --text:#555b61;
  --footer:#1c1c1e;
  --white:#ffffff;
}
*{box-sizing:border-box;margin:0;padding:0}
html,body{width:1200px;height:3979px;overflow:hidden}
body{position:relative;background:var(--white);font-family:'Roboto',sans-serif;color:var(--text)}
.abs{position:absolute}
.heading{font-family:'Montserrat',sans-serif}

/* header */
.site-header{position:absolute;left:0;top:0;width:1200px;height:108px;background:var(--white)}
.brand{position:absolute;display:flex;align-items:center;gap:12px;font-family:'Montserrat',sans-serif;font-weight:700;color:var(--navy);line-height:1.05;letter-spacing:.5px}
.brand-dot{width:44px;height:44px;border-radius:50%;background:var(--navy)}
.header-brand{left:111px;top:32px;font-size:19px}
.call-today{left:725px;top:12px;display:flex;gap:12px;align-items:center}
.icon-circle{display:flex;align-items:center;justify-content:center;border-radius:50%}
.call-today .icon-circle{width:32px;height:32px;background:var(--navy-dark)}
.call-today small{display:block;font-size:13px;font-weight:500;color:var(--ink)}
.call-today strong{display:block;font-size:21px;font-weight:500;color:var(--navy)}
.account{left:945px;top:22px;font-size:13px;font-weight:500;color:var(--orange)}
.main-nav{left:484px;top:70px;display:flex;gap:38px;font-size:15px;font-weight:500;color:var(--ink)}
.main-nav .active{color:var(--navy)}
.social{top:66px;width:30px;height:30px;border-radius:50%;background:var(--navy-dark)}

/* hero */
.hero{position:absolute;left:0;top:108px;width:1200px;height:680px}
.hero-box{position:absolute;left:295px;top:111px;width:610px;height:314px;background:rgba(30,30,32,.72);text-align:center;color:var(--white)}
.hero-box h1{font-family:'Montserrat',sans-serif;font-weight:800;font-size:62px;line-height:70px;margin-top:24px;letter-spacing:1px}
.hero-box p{font-size:20px;font-weight:500;margin-top:14px}
.btn-orange{display:inline-flex;align-items:center;gap:8px;background:var(--orange);color:var(--white);font-size:14px;font-weight:700;padding:13px 24px;border-radius:3px;margin-top:20px}

/* section titles */
.section-title{position:absolute;left:0;width:1200px;text-align:center;font-family:'Montserrat',sans-serif;font-weight:700;font-size:27px;color:var(--navy);letter-spacing:.5px}
.section-title span{color:var(--orange)}
.section-title::after{content:"";display:block;width:32px;height:3px;background:var(--navy);margin:10px auto 0}

/* services */
.service{position:absolute;width:300px;text-align:center}
.service .icon-circle{width:154px;height:154px;margin:0 auto;background:var(--navy)}
.service h3{font-family:'Montserrat',sans-serif;font-weight:700;font-size:17px;color:var(--navy);line-height:21px}
.service h3::after{content:"";display:block;width:34px;height:2px;background:var(--orange);margin:16px auto 0}
.service p{font-size:12.5px;line-height:20px;margin-top:20px;color:var(--text)}
.learn{display:inline-flex;align-items:center;gap:8px;font-size:12px;font-weight:500;text-decoration:underline;color:var(--navy);margin-top:18px}
.photo{background:linear-gradient(135deg,#c8d3dc,#7b8d9c 60%,#4e6273)}

/* who we are */
.who{left:638px;top:1716px;width:450px}
.who h2{font-family:'Montserrat',sans-serif;font-weight:700;font-size:26px;color:var(--navy)}
.who h2 span{color:var(--orange)}
.who h2::after{content:"";display:block;width:34px;height:3px;background:var(--orange);margin-top:14px}
.who p{font-size:14px;line-height:24px;text-align:justify;margin-top:22px}
.btn-navy{display:inline-flex;align-items:center;gap:8px;background:var(--navy);color:var(--white);font-size:12px;font-weight:700;padding:12px 24px;border-radius:2px;margin-top:24px}
.more-info{font-size:18px;font-weight:500;color:var(--orange);margin-top:20px}
.contact-row{display:flex;gap:30px;margin-top:16px}
.contact-item{display:flex;align-items:center;gap:14px}
.contact-item .icon-circle{width:32px;height:32px;background:var(--navy-dark)}
.contact-item small{display:block;font-size:13px;font-weight:500;color:var(--ink)}
.contact-item strong{display:block;font-size:21px;font-weight:500;color:var(--navy)}
.contact-item em{display:block;font-style:normal;font-size:14px;color:var(--navy)}

/* steps */
.step-card{position:absolute;left:111px;width:976px;height:235px;background:var(--white);border:1px solid #dfe4e8;border-radius:14px;box-shadow:0 2px 10px rgba(0,0,0,.1)}
.step-tab{position:absolute;width:122px;height:42px;background:var(--orange);color:var(--white);font-family:'Montserrat',sans-serif;font-weight:700;font-size:17px;display:flex;align-items:center;justify-content:center;letter-spacing:.5px}
.step-line{position:absolute;top:38px;height:160px;border-left:1px dashed #c7c7c7}
.step-art{position:absolute;top:16px;width:215px;height:202px;background:linear-gradient(135deg,#f4f7fa,#e3ecf3)}
.step-text{position:absolute;top:40px;width:550px}
.step-text h3{font-family:'Montserrat',sans-serif;font-weight:700;font-size:17px;color:var(--ink);letter-spacing:.3px}
.step-text h3::after{content:"";display:block;width:34px;height:2px;background:var(--orange);margin-top:14px}
.step-text p{font-size:14px;line-height:22.5px;text-align:justify;margin-top:16px}

/* footer */
.footer-brand{left:115px;top:3658px;font-size:20px;color:var(--white)}
.footer-brand .brand-dot{background:var(--white);width:48px;height:48px}
.footer-nav{left:440px;top:3673px;display:flex;gap:20px;font-family:'Montserrat',sans-serif;font-weight:700;font-size:14px;color:var(--white)}
.footer-nav i{font-style:normal;color:#cfcfcf}
.footer-contact{top:3770px;display:flex;align-items:center;gap:24px;color:var(--white)}
.footer-contact .icon-circle{width:60px;height:60px;background:var(--orange)}
.footer-contact h4{font-family:'Montserrat',sans-serif;font-size:14px;font-weight:700}
.footer-contact p{font-size:14px;line-height:20px;margin-top:4px}
.footer-contact strong{font-size:17px;font-weight:700;display:block;margin-top:4px}
.divider-v{top:3765px;width:1px;height:72px;background:#55585c}
.footer-rule{left:111px;top:3869px;width:976px;height:1px;background:#55585c}
.copyright{left:0;top:3914px;width:1200px;text-align:center;font-size:14px;color:var(--white)}
</style>
</head>
<body>

<!-- header -->
<header class="site-header">
  <div class="brand header-brand"><span class="brand-dot"></span><span>MERIDALE<br>PARTNERS</span></div>
  <div class="abs call-today">
    <span class="icon-circle"><svg width="14" height="14" viewBox="0 0 24 24"><path fill="#fff" d="M6.6 10.8a15 15 0 0 0 6.6 6.6l2.2-2.2c.3-.3.7-.4 1-.2 1.1.4 2.3.6 3.6.6.6 0 1 .4 1 1V20c0 .6-.4 1-1 1A17 17 0 0 1 3 4c0-.6.4-1 1-1h3.5c.6 0 1 .4 1 1 0 1.3.2 2.5.6 3.6.1.3 0 .7-.2 1z"/></svg></span>
    <div><small>Call Us Today !</small><strong>01 480 2175</strong></div>
  </div>
  <div class="abs account">&#9679; LOG IN &nbsp;/&nbsp; REGISTER</div>
  <nav class="abs main-nav"><span class="active">Home</span><span>About Us</span><span>Services</span><span>How We Do It</span><span>Contact Us</span></nav>
  <span class="abs social" style="left:1021px"></span>
  <span class="abs social" style="left:1059px"></span>
</header>

<!-- hero -->
<section class="hero">
  <div class="abs" role="img" aria-label="Upward view of glass office towers against the sky" style="left:0;top:0;width:1200px;height:680px;background:linear-gradient(160deg,#5d6e7d,#2e3b47 45%,#1b2530 70%,#44596b)"></div>
  <svg class="abs" style="left:0;top:420px" width="1200" height="270" viewBox="0 0 1200 270">
    <path d="M0 120 C170 260 360 330 610 200 C800 100 1000 0 1200 120 L1200 270 L0 270Z" fill="#fff"/>
    <path d="M0 120 C170 260 360 330 610 200 C760 120 860 80 960 60 C860 90 760 150 600 230 C380 330 170 280 0 150Z" fill="var(--navy)"/>
    <path d="M620 220 C800 120 1000 40 1200 120 L1200 150 C1060 60 900 100 620 220Z" fill="var(--orange)"/>
  </svg>
  <div class="hero-box">
    <h1>MERIDALE<br>PARTNERS</h1>
    <p>DATA ANALYTICS &amp; EPM CONSULTING SERVICES</p>
    <span class="btn-orange">GET STARTED <svg width="12" height="12" viewBox="0 0 12 12"><circle cx="6" cy="6" r="6" fill="#fff"/><path d="M5 3.5 7.5 6 5 8.5" stroke="var(--orange)" stroke-width="1.6" fill="none"/></svg></span>
  </div>
</section>

<!-- services -->
<h2 class="section-title" style="top:796px">OUR <span>SERVICES</span></h2>
<svg class="abs" style="left:0;top:900px" width="1200" height="220" viewBox="0 0 1200 220">
  <path d="M250 200 C330 90 450 50 560 40 M640 40 C760 50 880 90 950 200" stroke="#aaa" stroke-width="1.2" stroke-dasharray="3 3" fill="none"/>
  <path d="M388 80 l12 -6 -5 12" stroke="#888" fill="none"/>
  <path d="M805 80 l10 8 -12 2" stroke="#888" fill="none"/>
</svg>

<div class="service" style="left:449px;top:854px">
  <div class="icon-circle" style="background:var(--orange)"><svg width="70" height="70" viewBox="0 0 70 70"><path d="M35 12 L48 40 L35 58 L22 40Z" fill="none" stroke="#fff" stroke-width="4"/><circle cx="35" cy="38" r="4" fill="#fff"/><rect x="24" y="58" width="22" height="6" fill="#fff"/></svg></div>
  <h3 style="margin-top:8px">Design &amp; Implement</h3>
  <p>Working with the project management team, through each stage of the project, with clearly defined deliverables and well exercised plans to deliver them.</p>
  <span class="learn" style="color:var(--orange)">LEARN MORE ➔</span>
</div>

<div class="service" style="left:99px;top:1107px">
  <div class="icon-circle"><svg width="70" height="70" viewBox="0 0 70 70"><rect x="14" y="14" width="30" height="42" rx="3" fill="none" stroke="#fff" stroke-width="4"/><path d="M20 26h18M20 34h18M20 42h12" stroke="#fff" stroke-width="3"/><path d="M50 14 L42 58 M50 14 L58 58" stroke="#fff" stroke-width="4"/></svg></div>
  <h3 style="margin-top:26px">Advise &amp; Architect<br>Services</h3>
  <p>Helping our customers understand the art of the possible and safeguarding their investments by overseeing implementations.</p>
  <span class="learn">LEARN MORE ➔</span>
</div>

<div class="service" style="left:801px;top:1107px">
  <div class="icon-circle"><svg width="76" height="76" viewBox="0 0 76 76"><circle cx="38" cy="38" r="24" fill="none" stroke="#fff" stroke-width="7" stroke-dasharray="8 4"/><circle cx="38" cy="38" r="15" fill="none" stroke="#fff" stroke-width="3"/><path d="M30 44 l6 -6 4 4 8 -10" stroke="#fff" stroke-width="3" fill="none"/></svg></div>
  <h3 style="margin-top:26px">Optimize &amp; Manage</h3>
  <p>Our Managed Services delivers proactive, on-demand support for EPM and Data Analytics environments</p>
  <span class="learn">LEARN MORE ➔</span>
</div>

<div class="abs photo" role="img" aria-label="Consultant working on a laptop, framed in a circle" style="left:427px;top:1160px;width:346px;height:346px;border-radius:50%"></div>

<!-- who we are -->
<svg class="abs" style="left:0;top:1520px" width="1200" height="880" viewBox="0 0 1200 880">
  <path d="M0 140 C200 280 420 210 620 130 C820 40 1000 -20 1200 140 L1200 660 C1000 560 800 600 600 720 C400 830 160 800 0 690Z" fill="var(--ice)"/>
  <path d="M560 130 C760 20 1000 -30 1150 120 C1000 20 800 60 620 150Z" fill="var(--navy)"/>
  <path d="M0 60 C120 160 300 190 580 100 C330 220 120 180 0 80Z" fill="var(--orange)"/>
  <path d="M0 690 C160 800 400 830 600 720 C800 600 1000 560 1200 660 L1200 670 C1000 590 820 640 620 740 C420 860 160 820 0 720Z" fill="var(--navy)"/>
  <path d="M620 730 C800 620 1000 560 1200 640 L1200 660 C1040 600 860 640 620 730Z" fill="var(--orange)"/>
</svg>
<div class="abs" role="img" aria-label="Analytics dashboards on a monitor and laptop, framed in a circle" style="left:100px;top:1765px;width:448px;height:448px;border-radius:50%;border:3px solid #fff;background:linear-gradient(135deg,#e4ebf1,#9fb0bf 55%,#3d5366)"></div>

<div class="abs who">
  <h2>WHO WE <span>ARE</span></h2>
  <p>Meridale Partners is an exciting start-up in the Data Analytics and EPM space. Founded in 2019, MP specialise in the implementation and support of BI, EPM and Data Analytics business solutions, both in the Cloud and on-premise. Meridale Partners is an exciting start-up in the Data Analytics and EPM space. Founded in 2019, MP specialise in the implementation and support of BI, EPM and Data Analytics business solutions, both in the Cloud and on-premise.</p>
  <span class="btn-navy">LEARN MORE ➔</span>
  <div class="more-info">For More Information :</div>
  <div class="contact-row">
    <div class="contact-item"><span class="icon-circle"><svg width="14" height="14" viewBox="0 0 24 24"><path fill="#fff" d="M6.6 10.8a15 15 0 0 0 6.6 6.6l2.2-2.2c.3-.3.7-.4 1-.2 1.1.4 2.3.6 3.6.6.6 0 1 .4 1 1V20c0 .6-.4 1-1 1A17 17 0 0 1 3 4c0-.6.4-1 1-1h3.5c.6 0 1 .4 1 1 0 1.3.2 2.5.6 3.6.1.3 0 .7-.2 1z"/></svg></span><div><small>Call us on</small><strong>01 480 2175</strong></div></div>
    <div class="contact-item"><span class="icon-circle"><svg width="14" height="12" viewBox="0 0 14 12"><rect width="14" height="12" rx="1" fill="#fff"/><path d="M1 2l6 4 6-4" stroke="var(--navy-dark)" fill="none"/></svg></span><div><small>Email Us</small><em>info@meridale-partners.example</em></div></div>
  </div>
</div>

<!-- how we do it -->
<h2 class="section-title" style="top:2391px">HOW WE <span>DO IT</span></h2>

<div class="step-card" style="top:2475px">
  <div class="step-line" style="left:94px"></div>
  <div class="step-art" role="img" aria-label="Illustration of a magnifier over a bar chart" style="left:124px"></div>
  <div class="step-text" style="left:382px"><h3>LOREM IPSUM DOLOR SIT AMET, CONSECTETUR ADIPISCING</h3><p>Sed ut perspiciatis unde omnis iste natus error sit voluptatem accusantium doloremque laudantium, totam rem aperiam, eaque ipsa quae ab illo inventore veritatis et quasi architecto beatae vitae dicta sunt explicabo. Nemo enim ipsam voluptatem quia voluptas sit aspernatur aut odit aut fugit, sed quia consequuntur magni dolores eos qui ratione voluptatem sequi nesciunt.</p></div>
</div>
<div class="step-tab" style="left:145px;top:2455px">STEP - 01</div>

<div class="step-card" style="top:2764px">
  <div class="step-text" style="left:38px"><h3>LOREM IPSUM DOLOR SIT AMET, CONSECTETUR ADIPISCING</h3><p>Sed ut perspiciatis unde omnis iste natus error sit voluptatem accusantium doloremque laudantium, totam rem aperiam, eaque ipsa quae ab illo inventore veritatis et quasi architecto beatae vitae dicta sunt explicabo. Nemo enim ipsam voluptatem quia voluptas sit aspernatur aut odit aut fugit, sed quia consequuntur magni dolores eos qui ratione voluptatem sequi nesciunt.</p></div>
  <div class="step-art" role="img" aria-label="Illustration of a monitor showing charts" style="left:638px;width:196px"></div>
  <div class="step-line" style="left:883px"></div>
</div>
<div class="step-tab" style="left:934px;top:2745px">STEP - 02</div>

<div class="step-card" style="top:3053px">
  <div class="step-line" style="left:94px"></div>
  <div class="step-art" role="img" aria-label="Illustration of a colourful ring chart" style="left:124px;background:linear-gradient(135deg,#fff,#f1f5f9)"></div>
  <div class="step-text" style="left:382px"><h3>LOREM IPSUM DOLOR SIT AMET, CONSECTETUR ADIPISCING</h3><p>Sed ut perspiciatis unde omnis iste natus error sit voluptatem accusantium doloremque laudantium, totam rem aperiam, eaque ipsa quae ab illo inventore veritatis et quasi architecto beatae vitae dicta sunt explicabo. Nemo enim ipsam voluptatem quia voluptas sit aspernatur aut odit aut fugit, sed quia consequuntur magni dolores eos qui ratione voluptatem sequi nesciunt.</p></div>
</div>
<div class="step-tab" style="left:145px;top:3034px">STEP - 03</div>

<!-- footer -->
<svg class="abs" style="left:0;top:3380px" width="1200" height="599" viewBox="0 0 1200 599">
  <path d="M0 170 C200 300 420 230 620 150 C820 70 1000 10 1200 110 L1200 599 L0 599Z" fill="var(--footer)"/>
  <path d="M560 150 C760 60 980 10 1200 90 L1200 110 C1000 40 800 80 620 160Z" fill="var(--navy)"/>
  <path d="M0 120 C120 220 320 240 580 140 C330 270 120 240 0 150Z" fill="var(--orange)"/>
</svg>

<div class="brand abs footer-brand"><span class="brand-dot"></span><span>MERIDALE<br>PARTNERS</span></div>
<nav class="abs footer-nav"><span>HOME</span><i>|</i><span>ABOUT US</span><i>|</i><span>SERVICES</span><i>|</i><span>HOW WE DO IT</span><i>|</i><span>CONTACT US</span></nav>

<div class="abs footer-contact" style="left:149px">
  <span class="icon-circle"><svg width="18" height="24" viewBox="0 0 18 24"><path d="M9 0a9 9 0 0 0-9 9c0 7 9 15 9 15s9-8 9-15a9 9 0 0 0-9-9z" fill="#fff"/><circle cx="9" cy="9" r="3.5" fill="var(--orange)"/></svg></span>
  <div><h4>ADDRESS :</h4><p>14 Harbour Row, Quayside,<br>Dublin 4, D04 KP21</p></div>
</div>
<div class="abs divider-v" style="left:455px"></div>
<div class="abs footer-contact" style="left:495px">
  <span class="icon-circle"><svg width="22" height="16" viewBox="0 0 14 12"><rect width="14" height="12" rx="1" fill="#fff"/><path d="M1 2l6 4 6-4" stroke="var(--orange)" fill="none"/></svg></span>
  <div><h4>EMAIL :</h4><p>info@meridale-partners.example</p></div>
</div>
<div class="abs divider-v" style="left:832px"></div>
<div class="abs footer-contact" style="left:866px">
  <span class="icon-circle"><svg width="20" height="20" viewBox="0 0 24 24"><path fill="#fff" d="M6.6 10.8a15 15 0 0 0 6.6 6.6l2.2-2.2c.3-.3.7-.4 1-.2 1.1.4 2.3.6 3.6.6.6 0 1 .4 1 1V20c0 .6-.4 1-1 1A17 17 0 0 1 3 4c0-.6.4-1 1-1h3.5c.6 0 1 .4 1 1 0 1.3.2 2.5.6 3.6.1.3 0 .7-.2 1z"/></svg></span>
  <div><h4>CALL US :</h4><strong>01 480 2175</strong></div>
</div>
<div class="abs footer-rule"></div>
<div class="abs copyright">© 2022 Meridale Partners. All Rights Reserved</div>

</body>
</html>
```